EB-5 Regional Center needs a Web design

Harlow Ridge Financial Partners is an expanding EB-r regional center. We have been successful in sponsoring multiple projects of third-party developers and placing EB-5, B-1, and Private Investments into multiple projects.

We are now partnering directly with project developers in the energy and healthcare to raise foreign capital for projects in those industries. The foreign capital is used as project equity and our collective balance sheets are used to guarantee debt to complete the funding of the projects.

We need a web site where we can post our company credentials, the bios of each partner, a document page for each of our projects where we can post specific project related documents which foreign investors can read, and we will need a section where foreign investors can fill out investor forms confirming that they are qualified investors and leaving their contact so that our agents and executives can make contact.

The final design should reflect the exceptional experience of the partners and our financial strength and stability.

We do have a logo we would want to use on the web design.

Target Market(s)

EB-5 Investors, B-1 Investors, Private Equity and other investors seeking quality investment in job creating US projects.

Coding

Number of Pages Required

5+ page

Font styles to use
Sans Serif

Requirements
Must have
• Pages to display company info, partner bios, projects completed, and a projects in-process page where we can post documents and info on projects for which we are seeking foreign investment. We also need a section where investors can enter their qualifying personal information and leave contact information for us.

```html
<!DOCTYPE html>
<html lang="en">
<head>
<meta charset="utf-8">
<title>Harlow Ridge Financial Partners</title>
<link rel="stylesheet" href="https://fonts.googleapis.com/css2?family=Montserrat:wght@500;600;700&family=Roboto:wght@400;500;700;900&display=swap">
<style>
:root{
  --accent:#f7665a;
  --ink:#1f1f1f;
  --text:#555;
  --muted:#8a8a8a;
  --light:#efeff3;
  --line:#dcdcdc;
  --dark:#141414;
  --white:#fff;
}
*{box-sizing:border-box;margin:0;padding:0}
html,body{width:1200px;height:4713px;overflow:hidden}
body{position:relative;background:var(--white);font-family:'Roboto',sans-serif;color:var(--text)}
.abs{position:absolute}
.photo{position:absolute}
.heading{font-family:'Montserrat',sans-serif;font-weight:600;color:var(--ink);letter-spacing:-.5px}
.heading em{font-style:normal;color:var(--accent)}
.btn{position:absolute;background:var(--accent);color:#fff;font-size:11px;font-weight:700;text-transform:uppercase;display:flex;align-items:center;justify-content:center;border-radius:2px}
.para{font-size:13px;line-height:28.4px;color:var(--text)}

/* header */
.site-header{position:absolute;left:0;top:0;width:1200px;height:110px;border-top:3px solid #bdbdbd;background:#fff}
.brand{position:absolute;left:110px;top:36px;display:flex;align-items:center;gap:12px}
.brand-mark{width:30px;height:30px;background:#7d7d7d}
.brand-name{font-family:'Montserrat',sans-serif;font-weight:600;font-size:22px;color:#7d7d7d;letter-spacing:1px}
.main-nav{position:absolute;left:438px;top:56px;display:flex;gap:30px;font-size:12.5px;font-weight:500;color:#333}
.main-nav .active{color:var(--accent)}
.login{position:absolute;left:957px;top:40px;width:130px;height:46px;border:2px solid var(--accent);border-radius:24px;color:var(--accent);font-size:13px;font-weight:500;display:flex;align-items:center;justify-content:center}

/* hero */
.hero{position:absolute;left:0;top:110px;width:1200px;height:494px;overflow:hidden}
.hero .photo{inset:0;background:linear-gradient(100deg,#5b524c 0%,#8d8580 45%,#c9c6c4 65%,#9b938e 80%,#e5e3e2 100%)}
.hero-label{position:absolute;left:110px;top:112px;color:#fff;font-size:18px;letter-spacing:5px;font-weight:500}
.hero h1{position:absolute;left:110px;top:144px;width:460px;color:#fff;font-size:39px;line-height:39px;font-weight:900;text-transform:uppercase}
.hero p{position:absolute;left:110px;top:270px;width:440px;color:#fff;font-size:13px;line-height:26px;font-weight:500}
.slider-label{position:absolute;left:1072px;top:212px;color:#fff;font-size:13px}
.dot{position:absolute;left:1129px;width:14px;height:14px;border-radius:50%;background:#fff}

/* features */
.feature{position:absolute;top:668px;width:220px;text-align:center}
.feature svg{display:block;margin:0 auto}
.feature h3{margin-top:18px;font-size:15px;font-weight:500;color:#222}
.feature p{margin-top:11px;font-size:12.5px;line-height:25px;color:var(--muted)}

/* projects */
.projects{position:absolute;left:0;top:1322px;width:1200px;height:699px;background:var(--light)}
.tab{position:absolute;top:156px;height:59px;width:282px;display:flex;align-items:center;justify-content:center;font-size:19px;font-weight:500;color:#222}
.tab.active{background:var(--accent);color:#fff}
.card-img{position:absolute;top:251px;width:310px;height:189px}
.card-body{position:absolute;top:388px;width:287px;height:128px;background:#fff;box-shadow:0 2px 8px rgba(0,0,0,.08);padding:24px 27px}
.card-body h4{font-size:16px;line-height:28px;font-weight:500;color:#222}
.card-body .meta{margin-top:14px;font-size:12.5px;font-weight:700;color:#777}

/* contact */
.contact-bg{position:absolute;left:0;top:2530px;width:1200px;height:437px;background:linear-gradient(160deg,#3b3b40 0%,#25262b 50%,#4a4a4f 100%)}
.contact-box{position:absolute;left:112px;top:2758px;width:976px;height:260px;background:#fff;border:1px solid var(--line)}
.field{position:absolute;top:116px;height:59px;width:224px;border:1px solid #ddd;font-size:12.5px;color:#888;display:flex;align-items:center;padding-left:20px}

/* blogs */
.sub{position:absolute;top:3205px;font-size:16px;font-weight:500;color:#8f8f8f}
.arrow{position:absolute;top:3201px;width:25px;height:25px;border:1px solid #c8c8c8;border-radius:50%}
.arrow svg{position:absolute;left:6px;top:6px}
.blog-card{position:absolute;background:#fff;box-shadow:0 2px 10px rgba(0,0,0,.1)}
.date-tag{position:absolute;background:var(--accent);color:#fff;font-weight:700}
.blog-title{font-size:16.5px;line-height:28px;font-weight:500;color:#222}
.blog-text{font-size:12.5px;line-height:26px;color:#777}
.more{font-size:12px;font-weight:700;color:var(--accent)}
.comments{font-size:12px;color:#999}

/* partners */
.partner-img{position:absolute;top:3836px;width:475px;height:239px;border:1px solid var(--line)}
.partner-name{position:absolute;top:4098px;font-family:'Montserrat',sans-serif;font-size:23px;font-weight:500;color:#222}
.partner-name span{font-size:15px;margin-left:8px}
.partner-text{position:absolute;top:4134px;width:450px;font-size:12.5px;line-height:29px;color:#777}

/* footer */
.site-footer{position:absolute;left:0;top:4338px;width:1200px;height:375px;background:var(--dark);color:#fff}
.footer-title{position:absolute;top:80px;font-size:19px;font-weight:700}
.quick-links{position:absolute;left:548px;top:122px;list-style:none;font-size:13px;line-height:28.5px}
.quick-links li::before{content:"»";margin-right:10px}
.social{position:absolute;top:246px;width:30px;height:30px;border:1px solid #fff;border-radius:50%}
</style>
</head>
<body>

<header class="site-header">
  <div class="brand"><div class="brand-mark"></div><div class="brand-name">HARLOW RIDGE</div></div>
  <nav class="main-nav">
    <span class="active">HOME</span><span>ABOUT US</span><span>OUR PARTNERS</span><span>PROJECT</span><span>CONTACT US</span>
  </nav>
  <div class="login">LOG IN</div>
</header>

<section class="hero">
  <div class="photo" role="img" aria-label="Business partners shaking hands across a meeting table"></div>
  <svg class="abs" style="left:0;top:0" width="640" height="494"><polygon points="0,0 356,0 626,240 626,494 0,494" fill="#4a3f39" opacity=".88"/></svg>
  <div class="hero-label">HARLOW RIDGE</div>
  <h1>Find your path to a brighter financial future</h1>
  <p>Lorem ipsum dolor sit amet, consectetur adipiscing elit, sed do eiusmod tempor incididunt ut labore</p>
  <div class="btn" style="left:110px;top:334px;width:126px;height:36px">Get Started</div>
  <div class="slider-label">Slider 1</div>
  <div class="dot" style="top:212px;background:var(--accent)"></div>
  <div class="dot" style="top:240px"></div>
  <div class="dot" style="top:269px"></div>
</section>

<section class="features">
  <div class="feature" style="left:122px">
    <svg width="60" height="60" viewBox="0 0 60 60" fill="none" stroke="#222" stroke-width="2"><circle cx="16" cy="10" r="5"/><circle cx="30" cy="10" r="5"/><circle cx="44" cy="10" r="5"/><path d="M8 26v-6h44v6"/><rect x="6" y="30" width="48" height="24"/><circle cx="30" cy="42" r="7"/></svg>
    <h3>Lorem ipsum dolor</h3><p>Lorem ipsum dolor sit amet,<br>consectetur adipis</p>
  </div>
  <div class="feature" style="left:367px">
    <svg width="60" height="60" viewBox="0 0 60 60" fill="none" stroke="#222" stroke-width="2"><circle cx="14" cy="14" r="6"/><path d="M6 56V30h16v26"/><rect x="28" y="40" width="6" height="16"/><rect x="38" y="32" width="6" height="24"/><rect x="48" y="24" width="6" height="32"/><circle cx="40" cy="12" r="8"/><path d="M30 30l14-12"/></svg>
    <h3>Lorem ipsum dolor</h3><p>Lorem ipsum dolor sit amet,<br>consectetur adipis</p>
  </div>
  <div class="feature" style="left:611px">
    <svg width="60" height="60" viewBox="0 0 60 60" fill="none" stroke="#222" stroke-width="2"><rect x="18" y="4" width="24" height="44"/><line x1="10" y1="14" x2="50" y2="14"/><line x1="10" y1="38" x2="50" y2="38"/><circle cx="30" cy="26" r="6"/><path d="M24 48v8M36 48v8"/></svg>
    <h3>Lorem ipsum dolor</h3><p>Lorem ipsum dolor sit amet,<br>consectetur adipis</p>
  </div>
  <div class="feature" style="left:856px">
    <svg width="60" height="60" viewBox="0 0 60 60" fill="none" stroke="#222" stroke-width="2"><rect x="14" y="6" width="34" height="20" rx="2"/><circle cx="31" cy="16" r="5"/><path d="M4 42h10l12 6h14l14-10-4-4-12 6H26"/><path d="M4 54h14l8 2h16"/></svg>
    <h3>Lorem ipsum dolor</h3><p>Lorem ipsum dolor sit amet,<br>consectetur adipis</p>
  </div>
</section>

<section class="about">
  <h2 class="heading abs" style="left:110px;top:900px;font-size:37px">ABOUT <em>HARLOW RIDGE</em></h2>
  <div class="abs" style="left:0;top:957px;width:244px;height:1px;background:#bbb"></div>
  <p class="para abs" style="left:110px;top:972px;width:466px;text-align:justify">Lorem ipsum dolor sit amet, consectetur adipiscing elit, sed do eiusmod tempor incididunt ut labore et dolore magna aliqua. Ut enim ad minim veniam, quis nostrud exercitation ullamco laboris nisi ut aliquip ex ea commodo consequat. Duis aute irure dolor in reprehenderit in voluptate velit esse cillum dolore eu fugiat nulla pariatur. Excepteur sint occaecat cupidatat non proident, sunt in culpa qui officia deserunt mollit anim id est laborum.</p>
  <div class="btn" style="left:110px;top:1187px;width:126px;height:40px">Learn more »</div>
  <div class="photo" style="left:635px;top:909px;width:208px;height:289px;background:linear-gradient(160deg,#d9d9d9,#8e8e8e 60%,#e6e6e6)" role="img" aria-label="Two colleagues walking with a tablet in an office corridor"></div>
  <div class="photo" style="left:858px;top:938px;width:208px;height:289px;background:linear-gradient(160deg,#b9c4cc,#6e7f8d 55%,#d3d9de)" role="img" aria-label="Businesswoman presenting charts on a monitor"></div>
</section>

<section class="projects">
  <div class="abs" style="left:600px;top:0;width:1px;height:68px;background:#c9c9c9"></div>
  <h2 class="heading abs" style="left:0;width:1200px;text-align:center;top:86px;font-size:39px">OUR <em>PROJECTS</em></h2>
  <div class="tab" style="left:159px">LOREM IPSUM</div>
  <div class="tab active" style="left:459px">BANKING</div>
  <div class="tab" style="left:766px">LOREM IPSUM</div>

  <div class="photo card-img" style="left:112px;background:linear-gradient(135deg,#6b6b6b,#3b3b3b 50%,#9a9a9a)" role="img" aria-label="Businessman smiling in an office"></div>
  <div class="photo card-img" style="left:444px;background:linear-gradient(135deg,#9fb6cf,#4d6d93 50%,#c2d1e0)" role="img" aria-label="Bank building facade"></div>
  <div class="photo card-img" style="left:779px;background:linear-gradient(135deg,#c8c1bb,#6e5e55 50%,#ded7d2)" role="img" aria-label="Businesswoman at a meeting"></div>

  <div class="card-body" style="left:123px"><h4>Lorem ipsum dolor sit am et, consectetur</h4><div class="meta">COMPANY NAME &nbsp;|&nbsp; JAN 25, 2020</div></div>
  <div class="card-body" style="left:456px"><h4>Lorem ipsum dolor sit am et, consectetur</h4><div class="meta">COMPANY NAME &nbsp;|&nbsp; JAN 25, 2020</div></div>
  <div class="card-body" style="left:790px"><h4>Lorem ipsum dolor sit am et, consectetur</h4><div class="meta">COMPANY NAME &nbsp;|&nbsp; JAN 25, 2020</div></div>

  <div class="btn" style="left:536px;top:562px;width:128px;height:40px">View more »</div>
</section>

<section class="why">
  <div class="photo" style="left:132px;top:2144px;width:208px;height:289px;background:linear-gradient(170deg,#c7ccd1,#555a60 60%,#9aa0a6)" role="img" aria-label="Businessmen walking outside an office building"></div>
  <div class="photo" style="left:355px;top:2116px;width:208px;height:287px;background:linear-gradient(150deg,#d8d4d0,#5b5551 55%,#e4e0dc)" role="img" aria-label="Smiling business team in a meeting"></div>
  <h2 class="heading abs" style="left:624px;top:2108px;font-size:37px">WHY CHOOSE US?</h2>
  <div class="abs" style="left:970px;top:2164px;width:230px;height:1px;background:#bbb"></div>
  <p class="para abs" style="left:622px;top:2179px;width:468px;text-align:justify">Lorem ipsum dolor sit amet, consectetur adipiscing elit, sed do eiusmod tempor incididunt ut labore et dolore magna aliqua. Ut enim ad minim veniam, quis nostrud exercitation ullamco laboris nisi ut aliquip ex ea commodo consequat. Duis aute irure dolor in reprehenderit in voluptate velit esse cillum dolore eu fugiat nulla pariatur. Excepteur sint occaecat cupidatat non proident, sunt in culpa qui officia deserunt mollit anim id est laborum.</p>
  <div class="btn" style="left:622px;top:2396px;width:128px;height:38px">Learn more »</div>
</section>

<section class="contact">
  <div class="contact-bg" role="img" aria-label="Investors discussing documents at a desk"></div>
  <div class="contact-box">
    <h2 class="heading abs" style="left:0;width:976px;text-align:center;top:46px;font-size:37px">INVESTOR CONTACT FORM</h2>
    <div class="field" style="left:18px">Name*</div>
    <div class="field" style="left:256px">Address*</div>
    <div class="field" style="left:493px">Email Address*</div>
    <div class="btn" style="left:731px;top:116px;width:221px;height:59px;font-size:13px">Submit</div>
    <div class="abs" style="left:0;width:976px;text-align:center;top:201px;font-size:15px;color:var(--accent)">Have a any Questions?</div>
  </div>
</section>

<section class="blogs">
  <h2 class="heading abs" style="left:0;width:1200px;text-align:center;top:3130px;font-size:38px">EXPLORE OUR BLOGS</h2>
  <div class="sub" style="left:111px">MOST POPULAR BLOG</div>
  <div class="arrow" style="left:516px"><svg width="12" height="12"><path d="M8 2L4 6l4 4" stroke="#999" fill="none" stroke-width="1.5"/></svg></div>
  <div class="arrow" style="left:549px"><svg width="12" height="12"><path d="M4 2l4 4-4 4" stroke="#999" fill="none" stroke-width="1.5"/></svg></div>
  <div class="sub" style="left:611px">LATEST BLOG</div>
  <div class="arrow" style="left:1017px"><svg width="12" height="12"><path d="M8 2L4 6l4 4" stroke="#999" fill="none" stroke-width="1.5"/></svg></div>
  <div class="arrow" style="left:1050px"><svg width="12" height="12"><path d="M4 2l4 4-4 4" stroke="#999" fill="none" stroke-width="1.5"/></svg></div>

  <article class="blog-card" style="left:112px;top:3241px;width:473px;height:454px">
    <div class="photo" style="left:0;top:0;width:473px;height:258px;background:linear-gradient(140deg,#e2e2e2,#7a7a7a 55%,#3f3f3f)" role="img" aria-label="Hands reviewing financial charts beside a laptop"></div>
    <div class="date-tag" style="left:0;top:221px;width:124px;height:33px;font-size:14px;font-weight:500;display:flex;align-items:center;justify-content:center">JAN 25,2020</div>
    <div class="abs" style="left:34px;top:285px;width:410px">
      <div class="blog-title">Lorem ipsum dolor sit amet, consectet ur adipis cing elit, sed do eiusmod</div>
      <div class="blog-text" style="margin-top:2px">Lorem ipsum dolor sit amet, consectetur adipiscing elit, sed do eiusmod tempor incididunt ut labore et dolore</div>
    </div>
    <div class="abs more" style="left:34px;top:408px">Learn more ›</div>
    <div class="abs comments" style="left:350px;top:408px">22 Comments</div>
  </article>

  <article class="blog-card" style="left:611px;top:3241px;width:477px;height:212px">
    <div class="photo" style="left:0;top:0;width:218px;height:212px;background:linear-gradient(140deg,#c6cbd1,#5d6670 60%,#a9b0b8)" role="img" aria-label="Colleagues reviewing documents together"></div>
    <div class="date-tag" style="left:2px;top:2px;width:46px;height:46px;font-size:11px;line-height:17px;text-align:center;padding-top:6px">15<br>2020</div>
    <div class="abs" style="left:238px;top:16px;width:225px">
      <div class="blog-title">Lorem ipsum dolor sit am et, consectet ur</div>
      <div class="blog-text" style="font-size:11.5px;line-height:25px;margin-top:4px">Lorem ipsum dolor sit amet, cons ectetur adipiscing elit, sed do eius mod tempor incididunt ut</div>
    </div>
    <div class="abs more" style="left:238px;top:180px;font-size:11px">Learn more ›</div>
    <div class="abs comments" style="left:370px;top:180px;font-size:11px">22 Comments</div>
  </article>

  <article class="blog-card" style="left:611px;top:3482px;width:477px;height:213px">
    <div class="photo" style="left:0;top:0;width:218px;height:213px;background:linear-gradient(170deg,#c9b9bb,#6b5d58 60%,#3a3533)" role="img" aria-label="Miniature businessmen figures on stacked coins"></div>
    <div class="date-tag" style="left:2px;top:2px;width:46px;height:46px;font-size:11px;line-height:17px;text-align:center;padding-top:6px">15<br>2020</div>
    <div class="abs" style="left:238px;top:16px;width:225px">
      <div class="blog-title">Lorem ipsum dolor sit am et, consectet ur</div>
      <div class="blog-text" style="font-size:11.5px;line-height:25px;margin-top:4px">Lorem ipsum dolor sit amet, cons ectetur adipiscing elit, sed do eius mod tempor incididunt ut</div>
    </div>
    <div class="abs more" style="left:238px;top:181px;font-size:11px">Learn more ›</div>
    <div class="abs comments" style="left:370px;top:181px;font-size:11px">22 Comments</div>
  </article>
</section>

<section class="partners">
  <h2 class="heading abs" style="left:0;width:1200px;text-align:center;top:3767px;font-size:37px">OUR PARTNERSHIP</h2>
  <div class="photo partner-img" style="left:112px;background:linear-gradient(135deg,#f2f2f2,#9a9a9a 55%,#e0e0e0)" role="img" aria-label="Portrait of a smiling partner in glasses"></div>
  <div class="photo partner-img" style="left:613px;background:linear-gradient(135deg,#eef0ec,#7a837c 55%,#2f3b48)" role="img" aria-label="Portrait of a partner in an office"></div>
  <div class="partner-name" style="left:136px">DR.JOHN DOE<span>CEO, Company Name</span></div>
  <div class="partner-name" style="left:638px">DR.JOHN DOE<span>CEO, Company Name</span></div>
  <p class="partner-text" style="left:136px">Lorem ipsum dolor sit amet, consectetur adipiscing elit, sed do eiusmod tempor incididunt ut labore et dolore magna aliqua. Ut enim ad minim veniam, quis nostrud</p>
  <p class="partner-text" style="left:638px">Lorem ipsum dolor sit amet, consectetur adipiscing elit, sed do eiusmod tempor incididunt ut labore et dolore magna aliqua. Ut enim ad minim veniam, quis nostrud</p>
  <div class="abs more" style="left:136px;top:4231px">Learn more ›</div>
  <div class="abs more" style="left:638px;top:4231px">Learn more ›</div>
</section>

<footer class="site-footer">
  <div class="abs" style="left:110px;top:82px;display:flex;align-items:center;gap:12px">
    <div style="width:30px;height:30px;background:#fff"></div>
    <div style="font-family:'Montserrat',sans-serif;font-weight:600;font-size:24px;letter-spacing:1px">HARLOW RIDGE</div>
  </div>
  <p class="abs" style="left:110px;top:148px;width:290px;font-size:15px;line-height:28px">Lorem ipsum dolor sit amet, consec tetur adipiscing elit, sed do eiusmod tempor incididunt ut labore</p>
  <div class="social" style="left:111px"></div>
  <div class="social" style="left:150px"></div>
  <div class="social" style="left:188px"></div>

  <div class="footer-title" style="left:543px">QUICK LINKS</div>
  <ul class="quick-links">
    <li>Home</li><li>About us</li><li>Our Project</li><li>Partners</li><li>Why us?</li><li>Contact us</li>
  </ul>

  <div class="footer-title" style="left:776px">SUBSCRIBE THE NEWSLETTER</div>
  <p class="abs" style="left:778px;top:126px;width:310px;font-size:13px;line-height:25px">Lorem ipsum dolor sit amet, consectetur adipiscing elit, sed do eiusmod</p>
  <div class="abs" style="left:777px;top:183px;width:311px;height:41px;background:#fff;color:#999;font-size:12.5px;display:flex;align-items:center;padding-left:20px">Email Address</div>
  <div class="btn" style="left:777px;top:235px;width:123px;height:40px;font-size:12px">Subscribe</div>

  <div class="abs" style="left:110px;top:313px;width:978px;height:1px;background:#2c2c2c"></div>
  <div class="abs" style="left:0;width:1200px;text-align:center;top:331px;font-size:13px">© Copyrights 2020 Harlow Ridge Financial Partners | All Rights Reserved</div>
</footer>

</body>
</html>
```